Business Card design for law firm = Brightvale Australia

We are seeking a new design for our business cards.
We are keeping our logo, which is attached.
We need space for
Name
Title
Address is , which is
Level 7
214 Marlowe Street
Sydney NSW 2047
Phone :
Mobile :
Fax :
Email :
DX :
website www.brightvale-example.com.au

Industry/Entity Type

Law Firm / Banking and Finance

Contact Information for Business Card

We are seeking a new design for our business cards. We are keeping our logo. We need space for Name Title Address is Level 7 214 Marlowe Street Sydney NSW 2047 Phone Mobile Fax Email DX website www.brightvale-example.com.au

Colors
0054AA
0677BA
7BADD7
CADEEF
E8F1F8

Requirements
Must have
• see our website for general feel www.brightvale-example.com.au

```html
<!DOCTYPE html>
<html lang="en">
<head>
<meta charset="utf-8">
<title>Brightvale Australia — Business Card</title>
<link rel="stylesheet" href="https://fonts.googleapis.com/css2?family=Arimo:wght@400&family=Tinos:wght@400&display=swap">
<style>
  :root {
    --page-bg: #0e0e10;
    --card-bg: #28282b;
    --card-edge: #0a98d8;
    --brand-blue: #0677BA;
    --bright-blue: #0a98d8;
    --text-light: #f2f2f2;
    --serif: "Tinos", "Times New Roman", serif;
    --sans: "Arimo", Arial, sans-serif;
  }
  * { box-sizing: border-box; margin: 0; padding: 0; }
  html, body { width: 1200px; height: 820px; overflow: hidden; background: var(--page-bg); }
  .sheet { position: relative; width: 1200px; height: 820px; }

  .card {
    position: absolute; top: 253px; width: 550px; height: 314px;
    background: var(--card-bg);
    border-bottom: 3px solid var(--card-edge);
    border-left: 3px solid var(--card-edge);
  }
  .card--front { left: 35px; }
  .card--back { left: 615px; border: 3px solid var(--card-edge); }

  /* company name */
  .brand {
    position: absolute;
    font-family: var(--sans); font-weight: 400; color: var(--text-light);
    letter-spacing: 0.04em; line-height: 1; white-space: nowrap;
  }
  .card--front .brand { right: 30px; top: 66px; font-size: 28px; }
  .card--back .brand { left: 50%; top: 50%; transform: translate(-50%, -50%); font-size: 40px; }

  .rule {
    position: absolute; left: 92px; right: 30px; top: 168px;
    height: 1px; background: var(--bright-blue);
  }
  .person { position: absolute; left: 92px; top: 110px; color: var(--brand-blue); }
  .person__name { font-family: var(--serif); font-size: 27px; line-height: 1; }
  .person__title { font-family: var(--sans); font-size: 15px; margin-top: 3px; }

  .contacts { position: absolute; left: 92px; top: 180px; list-style: none; }
  .contacts li {
    display: flex; align-items: center; gap: 8px; height: 23px;
    font-family: var(--sans); font-size: 14px; color: var(--text-light); white-space: nowrap;
  }
  .contacts .icon {
    flex: none; width: 17px; height: 17px; background: var(--bright-blue);
    display: flex; align-items: center; justify-content: center;
  }
  .contacts .accent { color: var(--bright-blue); }

  .office {
    position: absolute; right: 30px; top: 180px; text-align: right; font-style: normal;
    font-family: var(--sans); font-size: 14px; line-height: 20px; color: var(--text-light);
  }
  .office__dx { margin-bottom: 16px; }
  .office__dx span { color: var(--bright-blue); }
</style>
</head>
<body>
<main class="sheet">
  <section class="card card--front" aria-label="Business card front">
    <p class="brand">Brightvale</p>

    <div class="person">
      <p class="person__name">Daniel Carter</p>
      <p class="person__title">Managing Director</p>
    </div>

    <div class="rule"></div>

    <ul class="contacts">
      <li><span class="icon"><svg width="11" height="11" viewBox="0 0 12 12"><path d="M2 1l2.5 0 1 3-1.5 1a6 6 0 0 0 3 3l1-1.5 3 1V10a1 1 0 0 1-1 1C5 11 1 7 1 2a1 1 0 0 1 1-1z" fill="#fff"/></svg></span><span>044-555 010 200</span></li>
      <li><span class="icon"><svg width="11" height="11" viewBox="0 0 12 12"><rect x="3" y="0.5" width="6" height="11" rx="1" fill="none" stroke="#fff" stroke-width="1.2"/><circle cx="6" cy="9.5" r="0.7" fill="#fff"/></svg></span><span>044-555 010 201</span></li>
      <li><span class="icon"><svg width="11" height="11" viewBox="0 0 12 12"><rect x="3" y="1" width="6" height="3" fill="#fff"/><rect x="1" y="4.5" width="10" height="4.5" fill="#fff"/><rect x="3" y="8" width="6" height="3" fill="#fff" stroke="#0a98d8" stroke-width="0.8"/></svg></span><span>044-555 010 202</span></li>
      <li><span class="icon"><svg width="11" height="11" viewBox="0 0 12 12"><rect x="1" y="2.5" width="10" height="7" fill="none" stroke="#fff" stroke-width="1.2"/><path d="M1 2.5l5 4 5-4" fill="none" stroke="#fff" stroke-width="1.2"/></svg></span><span>info@brightvale-example.com.au</span></li>
      <li><span class="icon"><svg width="11" height="11" viewBox="0 0 12 12"><circle cx="6" cy="6" r="5" fill="none" stroke="#fff" stroke-width="1.1"/><ellipse cx="6" cy="6" rx="2.2" ry="5" fill="none" stroke="#fff" stroke-width="1"/><path d="M1 6h10" stroke="#fff" stroke-width="1"/></svg></span><span>www.<span class="accent">brightvale-example</span>.com.au</span></li>
    </ul>

    <address class="office">
      <p class="office__dx"><span>DX :</span>555010</p>
      <p>Level 7, 214 Marlowe Street</p>
      <p>Sydney NSW 2047</p>
    </address>
  </section>

  <section class="card card--back" aria-label="Business card back">
    <p class="brand">Brightvale</p>
  </section>
</main>
</body>
</html>
```